Web Developer Needs a Business Card Design

I need a personal business card design that represents me as a web developer for potential employers. I would like the background to be a dark color on the front for contrast with my logo and name. The back will have all my information along with a smaller version of the logo. I want something with a modern look and feel, not too conservative. This will be used for potential employers and freelance work.

Industry/Entity Type

Business

Contact Information for Business Card

Front should have my logo and name. The back should have all my personal information which would include: name: Tom Varulek, phone: 570-614-3098, email: tomvarulek@quillbox.net, website url: www.tomvarulek.net, logo, web developer.

Font styles to use
Sans Serif

Requirements
Must have
• Must include my logo. The color palette base color will be the logo color.

```html
<!DOCTYPE html>
<html lang="en">
<head>
<meta charset="utf-8">
<title>Tom Varulek — Business Card</title>
<link rel="stylesheet" href="https://fonts.googleapis.com/css2?family=Source+Sans+3:wght@400;600&display=swap">
<style>
  :root {
    --backdrop: #e9ecec;
    --card: #ffffff;
    --mint: #4fe3c1;
    --ink: #1f1f1f;
    --shadow: rgba(0, 0, 0, 0.12);
  }
  * { margin: 0; padding: 0; box-sizing: border-box; }
  html, body {
    width: 1200px;
    height: 900px;
    overflow: hidden;
    background: var(--backdrop);
    font-family: "Source Sans 3", Arial, sans-serif;
  }
  .card {
    position: absolute;
    left: 122px;
    top: 156px;
    width: 956px;
    height: 588px;
    background: var(--card);
    border-radius: 28px;
    box-shadow: 0 10px 30px var(--shadow);
    overflow: hidden;
  }
  .accent-band {
    position: absolute;
    left: 34px;
    top: 0;
    width: 194px;
    height: 100%;
    background: var(--mint);
  }
  .brand-mark {
    position: absolute;
    left: 22px;
    top: 56px;
    width: 212px;
    height: 212px;
    border-radius: 50%;
    background: var(--card);
    display: flex;
    align-items: center;
    justify-content: center;
  }
  .brand-name {
    color: var(--mint);
    font-weight: 600;
    font-size: 34px;
  }
  .identity {
    position: absolute;
    left: 262px;
    top: 306px;
  }
  .person-name {
    color: var(--mint);
    font-weight: 600;
    font-size: 33px;
    line-height: 42px;
  }
  .person-role {
    color: var(--ink);
    font-size: 26px;
    line-height: 36px;
    margin-top: 4px;
  }
  .contact-list {
    position: absolute;
    left: 184px;
    top: 438px;
    list-style: none;
  }
  .contact-item {
    display: flex;
    align-items: center;
    height: 40px;
    color: var(--ink);
    font-size: 25px;
  }
  .contact-icon {
    width: 20px;
    height: 20px;
    margin-right: 58px;
    fill: var(--ink);
  }
</style>
</head>
<body>
  <main class="card">
    <div class="accent-band"></div>
    <div class="brand-mark"><span class="brand-name">Varulek</span></div>

    <div class="identity">
      <h1 class="person-name">Tom Varulek</h1>
      <p class="person-role">Front-End Developer</p>
    </div>

    <ul class="contact-list">
      <li class="contact-item">
        <svg class="contact-icon" viewBox="0 0 24 24" aria-hidden="true"><path d="M6.6 10.8a15.1 15.1 0 0 0 6.6 6.6l2.2-2.2a1 1 0 0 1 1-.25 11.4 11.4 0 0 0 3.6.57 1 1 0 0 1 1 1V20a1 1 0 0 1-1 1A17 17 0 0 1 3 4a1 1 0 0 1 1-1h3.5a1 1 0 0 1 1 1c0 1.25.2 2.45.57 3.57a1 1 0 0 1-.25 1z"/></svg>
        570-614-3098
      </li>
      <li class="contact-item">
        <svg class="contact-icon" viewBox="0 0 24 24" aria-hidden="true"><path d="M2 5h20v14H2z M4 7v.5l8 5 8-5V7l-8 5z" fill-rule="evenodd"/></svg>
        tomvarulek@quillbox.net
      </li>
      <li class="contact-item">
        <svg class="contact-icon" viewBox="0 0 24 24" aria-hidden="true" fill="none" stroke="#1f1f1f" stroke-width="2.6" stroke-linecap="round"><path d="M10 14a4 4 0 0 0 5.6 0l3.2-3.2a4 4 0 0 0-5.6-5.6l-1.2 1.2"/><path d="M14 10a4 4 0 0 0-5.6 0l-3.2 3.2a4 4 0 0 0 5.6 5.6l1.2-1.2"/></svg>
        www.tomvarulek.net
      </li>
    </ul>
  </main>
</body>
</html>
```